VORNAK SYSTEMS BUSINESS CARD DESIGN

WE WANT COMPLETE NEW DESIGN OF OUR BUSINESS CARD. WE ARE AN INTEGRATION COMPANY, WHERE WE INTEGRATE IOT/SMART SYSTEMS TO HOMES AND CORPORATE CUSTOMERS. WE SUPPLY AND INSTALL AUTOMATION PRODUCTS. THE FINAL DESIGN SHOULD COMMUNICATE TECHNOLOGY. THE CARD DESIGN SHOULD BE VERY IMPACT FULL. LOGO NEEDS TO BE THERE. IT WOULD NICE IF THE DESIGN WAS CLEAN. COLORS IS UP TO DESIGNER TO PLAY WITH, OR CAN STICK TO CORPORATE COLORS (FOLLOW LOGO). I HAVE ADDED FEW REFERENCE PHOTOS TO DRAW INSPIRATION MAYBE. I HAVE ADDED A HEX DESIGN, ITS NOT NECESSARY TO USE THIS DESIGN, ITS UPTO DESIGNER, JUST ADDED IF NEEDED TO PLAY WITH DESIGN.

Target Market(s)

Private end users and corporate clients

Industry/Entity Type

technology, home automation, home theaters, building management systems, IOT

Contact Information for Business Card

It should include Employee name, personal number, office number, email address, both in English and arabic. DETAILS TO INCLUDE :RAJESH PALLIVAL, MOBILE 0097150738265,OFFCIE 009714368547, RAJESH@VORNAKSYS.EXAMPLE

Requirements
Must have
• Should feel like a technology company from design. Details both and in English and arabic (or at least have provision for arabic in design).
Nice to have
• I would like logo on one side, and details on the other side. Logo design side should communicate technology with logo. Other side can be clean just with information or also have some design aspects following from logo side. it would be interesting to see submissions with square design as well (that looks like an app Icon). colors could be of logo, red black grey and white. I have added some designs to draw inspiration from

```html
<!DOCTYPE html>
<html lang="en">
<head>
<meta charset="utf-8">
<title>Vornak Systems – Business Card</title>
<link rel="stylesheet" href="https://fonts.googleapis.com/css2?family=Roboto:wght@400;500;700&family=Michroma&display=swap">
<style>
  :root {
    --stage: #2d2d2d;
    --card: #f1f1f1;
    --card-edge: #e2e2e2;
    --ink: #111111;
    --red: #d3121e;
    --white: #ffffff;
    --m-yellow: #e9c21b;
    --m-red: #d81d2a;
    --m-orange: #f0921c;
    --m-teal: #1aa9c7;
    --m-blue: #2c3a96;
    --m-purple: #3b1f5e;
  }
  * { box-sizing: border-box; margin: 0; padding: 0; }
  html, body { width: 1200px; height: 1138px; overflow: hidden; }
  body { background: var(--stage); font-family: "Roboto", sans-serif; position: relative; }

  .card {
    position: absolute;
    width: 620px;
    height: 376px;
    border-radius: 16px;
    background: linear-gradient(160deg, var(--white) 0%, var(--card) 55%, var(--card-edge) 100%);
    overflow: hidden;
  }
  .card--front { left: 272px; top: 184px; }
  .card--back  { left: 274px; top: 606px; }

  .brand { position: absolute; display: flex; align-items: center; gap: 10px; }
  .brand__dot { width: 20px; height: 20px; border-radius: 50%; background: var(--red); flex: none; }
  .brand__name { font-family: "Roboto", sans-serif; font-weight: 700; color: var(--ink); letter-spacing: 1px; white-space: nowrap; }

  /* Front */
  .card--front .brand { left: 46px; top: 118px; }
  .card--front .brand__name { font-size: 25px; }
  .tagline {
    position: absolute; left: 46px; top: 164px;
    font-family: "Michroma", sans-serif; font-size: 9.5px; letter-spacing: 1px; color: var(--ink);
    white-space: nowrap;
  }
  .mosaic-panel {
    position: absolute; left: 330px; top: 54px; width: 254px; height: 268px; border-radius: 14px;
    background:
      radial-gradient(circle at 75% 25%, var(--m-teal) 0%, transparent 45%),
      radial-gradient(circle at 20% 80%, var(--m-red) 0%, transparent 50%),
      radial-gradient(circle at 85% 85%, var(--m-purple) 0%, transparent 45%),
      linear-gradient(135deg, var(--m-yellow), var(--m-orange) 45%, var(--m-blue));
  }

  /* Back */
  .card--back .brand { left: 26px; top: 52px; gap: 14px; }
  .card--back .brand__dot { width: 34px; height: 34px; }
  .card--back .brand__name { font-size: 46px; letter-spacing: 2px; }
  .person { position: absolute; left: 22px; top: 156px; font-size: 25px; font-weight: 500; color: var(--red); }
  .contacts { position: absolute; left: 22px; top: 206px; font-size: 16px; color: var(--ink); }
  .contacts__row { display: flex; align-items: center; height: 26px; }
  .contacts__row + .contacts__row { margin-top: 2px; }
  .icon { width: 16px; height: 16px; flex: none; margin-right: 20px; }
  .contacts__office { display: flex; align-items: center; margin-left: 24px; }
  .wave-band { position: absolute; left: 0; bottom: 0; width: 620px; height: 142px; }
  .division {
    position: absolute; right: 28px; bottom: 22px; text-align: right;
    font-family: "Michroma", sans-serif; font-size: 15px; line-height: 21px; letter-spacing: 2px; color: var(--white);
  }
</style>
</head>
<body>

<section class="card card--front">
  <div class="brand">
    <span class="brand__dot"></span>
    <span class="brand__name">VORNAK SYSTEMS</span>
  </div>
  <p class="tagline">A VORNAK GROUP DIVISION.</p>
  <div class="mosaic-panel" role="img" aria-label="Colourful faceted crystal mosaic in red, yellow, teal and violet"></div>
</section>

<section class="card card--back">
  <div class="brand">
    <span class="brand__dot"></span>
    <span class="brand__name">VORNAK SYSTEMS</span>
  </div>

  <h1 class="person">Rajesh Pallival</h1>

  <div class="contacts">
    <div class="contacts__row">
      <svg class="icon" viewBox="0 0 16 16" fill="none" stroke="var(--red)" stroke-width="1.6"><rect x="4" y="1" width="8" height="14" rx="1.5"/><line x1="7" y1="12.5" x2="9" y2="12.5"/></svg>
      <span>0097150738265</span>
      <span class="contacts__office">
        <svg class="icon" viewBox="0 0 16 16" fill="none" stroke="var(--red)" stroke-width="1.6"><circle cx="8" cy="8" r="6.8"/><path d="M5.5 4.5l1.5 1.5-1 1.2c.6 1.3 1.5 2.2 2.8 2.8l1.2-1 1.5 1.5-1 1.2c-2.8-.3-5.2-2.7-5.5-5.5z" fill="var(--red)" stroke="none"/></svg>
        <span>009714368547</span>
      </span>
    </div>
    <div class="contacts__row">
      <svg class="icon" viewBox="0 0 16 16" fill="none" stroke="var(--red)" stroke-width="1.5"><rect x="1" y="3.5" width="14" height="9" rx="1"/><path d="M1.5 4l6.5 5 6.5-5"/></svg>
      <span>rajesh@vornaksys.example</span>
    </div>
    <div class="contacts__row">
      <svg class="icon" viewBox="0 0 16 16" fill="none" stroke="var(--red)" stroke-width="1.4"><circle cx="8" cy="8" r="6.8"/><ellipse cx="8" cy="8" rx="3" ry="6.8"/><line x1="1.2" y1="8" x2="14.8" y2="8"/></svg>
      <span>www.vornaksys.example</span>
    </div>
  </div>

  <svg class="wave-band" viewBox="0 0 620 142" role="img" aria-label="Flowing band of colourful faceted crystal mosaic">
    <defs>
      <linearGradient id="band-fill" x1="0" y1="0" x2="1" y2="0">
        <stop offset="0" stop-color="var(--m-yellow)"/>
        <stop offset="0.3" stop-color="var(--m-red)"/>
        <stop offset="0.55" stop-color="var(--m-orange)"/>
        <stop offset="0.8" stop-color="var(--m-teal)"/>
        <stop offset="1" stop-color="var(--m-blue)"/>
      </linearGradient>
      <linearGradient id="band-shade" x1="0" y1="0" x2="0" y2="1">
        <stop offset="0" stop-color="var(--m-purple)" stop-opacity="0"/>
        <stop offset="1" stop-color="var(--m-purple)" stop-opacity="0.4"/>
      </linearGradient>
    </defs>
    <path d="M0 62 C110 100 210 96 290 50 S470 -4 620 4 L620 142 L0 142 Z" fill="url(#band-fill)"/>
    <path d="M0 62 C110 100 210 96 290 50 S470 -4 620 4 L620 142 L0 142 Z" fill="url(#band-shade)"/>
    <path d="M0 80 C120 120 220 110 300 60 S480 10 620 14" fill="none" stroke="var(--white)" stroke-width="7"/>
    <path d="M0 96 C130 136 240 126 320 74 S490 24 620 30" fill="none" stroke="var(--white)" stroke-width="3" opacity="0.85"/>
  </svg>

  <p class="division">A VORNAK<br>GROUP DIVISION</p>
</section>

</body>
</html>
```